Front and content page design for Fitness Cookbook

I am looking for someone to Design a front cover for a Recipe book and also create an amazing layout for the book.

Its for a corporate seminar so has to be eye catching, professional and bold.

Content is complete

Target Market(s)

Industry/Entity Type

Health And Wellness

Font styles to use
Sans Serif

Requirements
Must have
• Eye catching, professional and bold.
• By Dorian as stated on the document
• Must have Tidewell Motion Logo on it.

```html
<!DOCTYPE html>
<html lang="en">
<head>
<meta charset="utf-8">
<title>Homemade Beef Burgers</title>
<link rel="stylesheet" href="https://fonts.googleapis.com/css2?family=Cabin:wght@400;500;600&display=swap">
<style>
  :root {
    --page: #ffffff;
    --orange: #f7941d;
    --blue: #1d8fd1;
    --ink: #3a3a3a;
    --photo-top: #efece8;
    --photo-mid: #8a6a55;
    --photo-low: #d8d4cf;
  }
  * { margin: 0; padding: 0; box-sizing: border-box; }
  html, body { width: 849px; height: 1200px; overflow: hidden; background: var(--page); }
  .page {
    position: relative;
    width: 849px;
    height: 1200px;
    font-family: "Cabin", sans-serif;
    color: var(--ink);
  }
  .recipe-photo {
    position: absolute;
    left: 70px; top: 18px;
    width: 710px; height: 460px;
    background: radial-gradient(ellipse at 50% 62%, var(--photo-mid) 0%, #a98d78 32%, var(--photo-low) 62%, var(--photo-top) 100%);
  }
  .title-band {
    position: absolute;
    left: 0; top: 504px;
    width: 849px; height: 204px;
    background: var(--orange);
    display: flex; align-items: center; justify-content: center;
  }
  .title-band h1 {
    font-weight: 400;
    font-size: 54px;
    color: #fff;
    letter-spacing: 0.5px;
  }
  .content {
    position: absolute;
    left: 57px; top: 732px;
    width: 740px;
    font-size: 14.5px;
    line-height: 17px;
  }
  .label {
    color: var(--blue);
    font-weight: 500;
    text-transform: uppercase;
    font-size: 15.5px;
  }
  .timing p { margin: 0; }
  .ingredients { margin-top: 18px; }
  .ingredients ul { list-style: none; }
  .method { margin-top: 24px; }
  .method p { margin-top: 4px; line-height: 18px; }
  .page-footer {
    position: absolute;
    left: 20px; top: 1145px;
    display: flex; align-items: center; gap: 10px;
    font-size: 14px;
  }
  .brand { display: flex; align-items: center; gap: 5px; color: var(--blue); font-size: 12px; }
  .brand-dot { width: 10px; height: 10px; border-radius: 50%; background: var(--blue); }
</style>
</head>
<body>
<div class="page">
  <div class="recipe-photo" role="img" aria-label="Photo of two homemade beef burger patties topped with spinach and beetroot slices"></div>

  <header class="title-band">
    <h1>Homemade Beef Burgers</h1>
  </header>

  <main class="content">
    <section class="timing">
      <p><span class="label">Prep time</span> 5 mins</p>
      <p><span class="label">Cooking time</span> 20 mins</p>
    </section>

    <section class="ingredients">
      <p><span class="label">Ingredients</span> Makes 3-4 burgers</p>
      <ul>
        <li>500g grass fed lean beef mince</li>
        <li>1 whole egg</li>
        <li>1 egg white</li>
        <li>1tsp coconut oil</li>
        <li>1/2 cup onions</li>
        <li>2 cloves garlic</li>
        <li>2 fresh chillies (optional)</li>
        <li>Salt, pepper, mixed herbs to taste 2 handful of spinach</li>
        <li>4 slices of beetroot</li>
      </ul>
    </section>

    <section class="method">
      <h2 class="label">Cooking instructions</h2>
      <p>Mash the egg and egg white into the mince and add the onions, garlic, chillies and spices in the same bowl. Use your hands to mould the mixture into 3-4 patties. Fry the patties in the coconut oil on a medium heat, turning throughout till cooked. Layer the spinach and beetroot on top of each one.</p>
    </section>
  </main>

  <footer class="page-footer">
    <span class="page-number">6</span>
    <span class="brand"><span class="brand-dot"></span>Tidewell Motion</span>
  </footer>
</div>
</body>
</html>
```